Professional Photography Business cards

I need business cards that include my logo which I have uploaded. I run a photography business. I am open to ideas but I would like one side to have my logo and the other side to have my contact info. I don't have a website made but I do own a website domain. I have uploaded 2 different logo color schemes. My business colors are Blue, black , and white.

Business Name
Business Phone Number
Business Email
Business Website address
Instagram

Industry/Entity Type

Professional Photography

Contact Information for Business Card

Phone Number: 916-384-7702 email: info@tlane-studio.example Instagram: @t.lanestudio website doman- www.tlane-studio.example

Requirements
Must have
• I like the idea of a business card with a full black background front and back of card. My colors must include royal blue, black, and white

```html
<!DOCTYPE html>
<html lang="en">
<head>
<meta charset="utf-8">
<title>T. Lane Studio — Business Cards</title>
<link rel="stylesheet" href="https://fonts.googleapis.com/css2?family=Arimo:wght@400&display=swap">
<style>
  :root {
    --backdrop: #2b2b2b;
    --royal-blue: #0a14a6;
    --brand-blue: #1a22d0;
    --card-black: #050505;
    --white: #ffffff;
    --shadow: rgba(0, 0, 0, 0.55);
    --glow-front: rgba(80, 100, 255, 0.22);
    --glow-back: rgba(255, 255, 255, 0.07);
  }
  * { box-sizing: border-box; margin: 0; padding: 0; }
  html, body {
    width: 1200px;
    height: 1015px;
    overflow: hidden;
    background: var(--backdrop);
    font-family: "Arimo", Arial, sans-serif;
  }
  .canvas {
    position: relative;
    width: 1200px;
    height: 1015px;
  }
  .card {
    position: absolute;
    width: 600px;
    height: 343px;
    box-shadow: 0 14px 30px var(--shadow);
    overflow: hidden;
  }
  .card__decoration {
    position: absolute;
    border-radius: 50%;
    pointer-events: none;
  }
  /* Logo side */
  .card--front {
    left: 60px;
    top: 120px;
    background: var(--royal-blue);
  }
  .card--front .card__decoration {
    left: 250px;
    top: 20px;
    width: 300px;
    height: 300px;
    background: radial-gradient(circle, var(--glow-front) 0%, rgba(80, 100, 255, 0.08) 55%, transparent 72%);
  }
  .brand {
    position: absolute;
    display: flex;
    align-items: center;
    gap: 16px;
  }
  .card--front .brand {
    left: 50%;
    top: 50%;
    transform: translate(-50%, -50%);
  }
  .brand__mark {
    width: 18px;
    height: 18px;
    border-radius: 50%;
    background: var(--white);
  }
  .brand__name {
    font-size: 44px;
    color: var(--white);
    letter-spacing: 1px;
    white-space: nowrap;
  }
  /* Contact side */
  .card--back {
    left: 540px;
    top: 540px;
    background: var(--card-black);
  }
  .card--back .card__decoration {
    left: 60px;
    top: 60px;
    width: 320px;
    height: 320px;
    background: radial-gradient(circle, var(--glow-back) 0%, rgba(255, 255, 255, 0.03) 55%, transparent 72%);
  }
  .card--back .brand {
    right: 40px;
    top: 54px;
    gap: 12px;
  }
  .card--back .brand__mark { background: var(--brand-blue); width: 14px; height: 14px; }
  .card--back .brand__name { color: var(--brand-blue); font-size: 32px; }
  .contact-list {
    position: absolute;
    left: 40px;
    bottom: 36px;
    list-style: none;
    display: flex;
    flex-direction: column;
    gap: 12px;
  }
  .contact-list li,
  .social {
    display: flex;
    align-items: center;
    gap: 12px;
    color: var(--white);
    font-size: 18px;
  }
  .icon {
    width: 24px;
    height: 24px;
    flex: none;
  }
  .social {
    position: absolute;
    right: 40px;
    top: 168px;
  }
  .social__dot {
    width: 22px;
    height: 22px;
    border-radius: 50%;
    background: var(--brand-blue);
    flex: none;
  }
</style>
</head>
<body>
<main class="canvas">
  <section class="card card--front" aria-label="Business card, logo side">
    <div class="card__decoration" role="img" aria-label="Faint brand emblem decoration"></div>
    <div class="brand">
      <span class="brand__mark"></span>
      <span class="brand__name">T. Lane Studio</span>
    </div>
  </section>

  <section class="card card--back" aria-label="Business card, contact side">
    <div class="card__decoration" role="img" aria-label="Faint brand emblem decoration"></div>
    <div class="brand">
      <span class="brand__mark"></span>
      <span class="brand__name">T. Lane Studio</span>
    </div>

    <div class="social">
      <span>@t.lanestudio</span>
      <span class="social__dot"></span>
    </div>

    <ul class="contact-list">
      <li>
        <svg class="icon" viewBox="0 0 24 24" aria-hidden="true">
          <circle cx="12" cy="12" r="12" fill="var(--brand-blue)"/>
          <path d="M8.5 6.5l2 2.2-1.2 1.4c.8 1.7 2 2.9 3.6 3.7l1.4-1.2 2.2 2-1.3 1.9c-3.9-.5-7.3-3.9-7.9-7.9z" fill="#000"/>
        </svg>
        <span>916-384-7702</span>
      </li>
      <li>
        <svg class="icon" viewBox="0 0 24 24" aria-hidden="true">
          <circle cx="12" cy="12" r="12" fill="var(--brand-blue)"/>
          <rect x="6" y="8" width="12" height="8" fill="#000"/>
          <path d="M6 8l6 4.5L18 8" fill="none" stroke="var(--brand-blue)" stroke-width="1.2"/>
        </svg>
        <span>info@tlane-studio.example</span>
      </li>
      <li>
        <svg class="icon" viewBox="0 0 24 24" aria-hidden="true">
          <circle cx="12" cy="12" r="12" fill="var(--brand-blue)"/>
          <g fill="none" stroke="#000" stroke-width="1.2">
            <circle cx="12" cy="12" r="6"/>
            <ellipse cx="12" cy="12" rx="2.6" ry="6"/>
            <path d="M6 12h12M7 9h10M7 15h10"/>
          </g>
        </svg>
        <span>www.tlane-studio.example</span>
      </li>
    </ul>
  </section>
</main>
</body>
</html>
```